Stylish Business Cards Wanted

- DOUBLE SIDED Design Required -

High end, edgy cards for a corporate and personal stylist. Must include logo,
Name: Belinda Harwick
Title: Director and Stylist
telephone : +61 8 7142 5809
email: belinda@theloombriefing.example
website: theloombriefing.example
Tag: Corporate Workwear & Uniform Specialist | Personal Stylist
Would like nice icons for telephone, email, website

Target Market(s)

Businesses wanting stylish uniforms, people wanting stylish wardrobes

Industry/Entity Type

Corporate Workwear Stylist

Contact Information for Business Card

I would like black, white and gold foiling incorporated in the design - possibly a touch of the other colours on my branding guide attached Name: Belinda Harwick Title: Director and Stylist telephone : +61 8 7142 5809 email: belinda@theloombriefing.example website: theloombriefing.example Tag: Corporate Workwear & Uniform Specialist | Personal Stylist Would like nice icons for telephone, email, website

Font styles to use
Other font styles liked:
• Raleway

Colors

Designer to choose colors to be used in the design.

Requirements
Must have
• Gold foil accents

```html
<!DOCTYPE html>
<html lang="en">
<head>
<meta charset="utf-8">
<title>The Loom Briefing – Business Cards</title>
<link rel="stylesheet" href="https://fonts.googleapis.com/css2?family=Arimo&family=Lato:wght@400;700&family=Raleway:wght@600&display=swap">
<style>
  :root {
    --ink: #231f20;
    --gold: #e3bd5a;
    --paper: #ffffff;
    --mist: #dfe1e0;
    --rule: #8c8c8c;
    --backdrop: #a3a3a3;
  }
  * { box-sizing: border-box; margin: 0; padding: 0; }
  html, body { width: 1200px; height: 1200px; overflow: hidden; }
  body { background: var(--backdrop); position: relative; }

  .card {
    position: absolute;
    top: 303px;
    height: 594px;
    overflow: hidden;
  }
  .card--front { left: 200px; width: 370px; background: var(--ink); }
  .card--back { left: 599px; width: 364px; background: var(--paper); }

  .front-band { position: absolute; inset: 0; width: 100%; height: 100%; }

  .brand-name {
    position: absolute;
    left: 0; right: 0;
    text-align: center;
    font-family: "Raleway", sans-serif;
    font-weight: 600;
    line-height: 1.05;
  }
  .card--front .brand-name {
    top: 196px;
    font-size: 50px;
    color: var(--mist);
  }
  .card--back .brand-name {
    top: 120px;
    font-size: 34px;
    color: var(--ink);
  }

  .tagline {
    position: absolute;
    left: 0; right: 0;
    top: 498px;
    text-align: center;
    font-family: "Arimo", sans-serif;
    font-size: 16.5px;
    line-height: 22px;
    color: var(--ink);
  }

  .person { position: absolute; left: 0; right: 0; top: 386px; text-align: center; }
  .person__name {
    font-family: "Lato", sans-serif;
    font-weight: 700;
    font-size: 25px;
    letter-spacing: -0.2px;
    color: var(--ink);
  }
  .person__title {
    font-family: "Arimo", sans-serif;
    font-size: 14.5px;
    color: var(--gold);
    margin-top: 2px;
  }

  .icon-row {
    position: absolute;
    top: 460px;
    left: 87px;
    width: 190px;
    height: 25px;
    display: flex;
    align-items: center;
    gap: 4px;
  }
  .icon-row__rule { flex: 1; height: 1px; background: var(--rule); }
  .icon-row__rule--left { margin-right: 4px; }
  .icon-row__rule--right { margin-left: 4px; }
  .icon { width: 25px; height: 25px; display: block; }

  .contact {
    position: absolute;
    left: 0; right: 0;
    top: 493px;
    text-align: center;
    font-family: "Arimo", sans-serif;
    font-size: 16px;
    line-height: 22px;
    color: var(--ink);
    list-style: none;
  }
</style>
</head>
<body>

<section class="card card--front" aria-label="Card front">
  <svg class="front-band" viewBox="0 0 370 594" preserveAspectRatio="none" aria-hidden="true">
    <path d="M0 361 C 120 360, 260 350, 370 305 L370 594 L0 594 Z" fill="var(--gold)"/>
  </svg>
  <p class="brand-name">The Loom<br>Briefing</p>
  <p class="tagline">Corporate Workwear &amp; Uniform Specialist<br>Personal Stylist</p>
</section>

<section class="card card--back" aria-label="Card back">
  <p class="brand-name">The Loom<br>Briefing</p>

  <div class="person">
    <h1 class="person__name">BELINDA HARWICK</h1>
    <p class="person__title">DIRECTOR AND STYLIST</p>
  </div>

  <div class="icon-row" aria-hidden="true">
    <span class="icon-row__rule icon-row__rule--left"></span>
    <svg class="icon" viewBox="0 0 25 25">
      <rect width="25" height="25" rx="4" fill="var(--ink)"/>
      <path d="M6 9.5 C6 7, 19 7, 19 9.5 L17 11 L15.5 9.5 L9.5 9.5 L8 11 Z" fill="#fff"/>
      <rect x="8" y="11.5" width="9" height="7" rx="1" fill="#fff"/>
      <circle cx="12.5" cy="15" r="1.6" fill="var(--ink)"/>
    </svg>
    <svg class="icon" viewBox="0 0 25 25">
      <rect width="25" height="25" rx="4" fill="var(--ink)"/>
      <rect x="5.5" y="8" width="14" height="10" fill="none" stroke="#fff" stroke-width="1.3"/>
      <path d="M5.5 8 L12.5 13.5 L19.5 8 M5.5 18 L10.5 12 M19.5 18 L14.5 12" fill="none" stroke="#fff" stroke-width="1.1"/>
    </svg>
    <svg class="icon" viewBox="0 0 25 25">
      <rect width="25" height="25" rx="4" fill="var(--ink)"/>
      <circle cx="12.5" cy="12.5" r="6.5" fill="none" stroke="#fff" stroke-width="1.4"/>
      <ellipse cx="12.5" cy="12.5" rx="2.8" ry="6.5" fill="none" stroke="#fff" stroke-width="1"/>
      <path d="M6 12.5 H19" stroke="#fff" stroke-width="1"/>
    </svg>
    <span class="icon-row__rule icon-row__rule--right"></span>
  </div>

  <ul class="contact">
    <li>+61 8 7142 5809</li>
    <li>belinda@theloombriefing.example</li>
    <li>theloombriefing.example</li>
  </ul>
</section>

</body>
</html>
```